Billboard design 8x3M RAVU (Spanish company)

We´re located in the south of Spain. We run a local telecom company.
We sell Fiber optic, and mobile phone lines mainly.
The billboard will have to be in Spanish, I would like the price to be something you spot on first sight when passing by in the car.
Our company color is blue, like in our logo which I will add. I will also add a example from what we currently have.
The new offer should be:
1000 megas + 100Gigas movil con llamadas ilimitadas. (meaning 1000Mb fiber optic speed and 100Gb data and unlimited calls for 1 mobile line)
Our details are: phone line 958 47 6620
Website: ra-vu.es

```html
<!DOCTYPE html>
<html lang="es">
<head>
<meta charset="utf-8">
<title>RAVU – Valla 8x3</title>
<link rel="stylesheet" href="https://fonts.googleapis.com/css2?family=Exo+2:wght@600;700;800&display=swap">
<style>
  :root {
    --navy: #0d4f85;
    --sky: #1ab3ea;
    --yellow: #fcc934;
    --amber: #f5ab22;
    --white: #ffffff;
    --backdrop: #e9eef2;
  }
  html, body {
    margin: 0;
    padding: 0;
    width: 1200px;
    height: 874px;
    overflow: hidden;
    background: var(--backdrop);
  }
  .billboard {
    position: absolute;
    left: 0;
    top: 220px;
    width: 1200px;
    height: 433px;
    display: block;
  }
  .billboard text { font-family: "Exo 2", sans-serif; }
  .price-amount { font-weight: 800; fill: var(--white); }
  .price-label { font-weight: 700; fill: var(--white); }
  .offer-main { font-weight: 700; fill: var(--navy); }
  .offer-sub { font-weight: 600; fill: var(--sky); }
  .contact-line { font-weight: 700; fill: var(--navy); }
  .brand-name { font-weight: 800; fill: var(--sky); }
  .brand-tagline { font-weight: 700; }
  .tag-light { fill: var(--sky); }
  .tag-dark { fill: var(--navy); }
</style>
</head>
<body>
<svg class="billboard" viewBox="0 0 1200 433" xmlns="http://www.w3.org/2000/svg">
  <defs>
    <linearGradient id="board-fade" x1="0" y1="0" x2="1" y2="0">
      <stop offset="0.55" stop-color="#ffffff"/>
      <stop offset="0.66" stop-color="#fcc934"/>
      <stop offset="1" stop-color="#f7b52a"/>
    </linearGradient>
    <linearGradient id="photo-tone" x1="0" y1="0" x2="1" y2="1">
      <stop offset="0" stop-color="#f8bd33"/>
      <stop offset="1" stop-color="#f29e1e"/>
    </linearGradient>
    <clipPath id="board-clip"><rect width="1200" height="433"/></clipPath>
  </defs>

  <g clip-path="url(#board-clip)">
    <!-- board surface -->
    <rect class="board-surface" width="1200" height="433" fill="url(#board-fade)"/>

    <!-- photo area: smiling support agent with headset holding a laptop -->
    <path class="hero-photo" role="img" aria-label="Fotografía de una agente de atención al cliente sonriente con auriculares, sosteniendo un portátil y señalando la oferta"
          d="M990,0 H1200 V398 H770 V150 H990 Z" fill="url(#photo-tone)"/>

    <!-- price badge -->
    <g class="price-badge">
      <circle cx="367" cy="35" r="167" fill="var(--navy)" stroke="var(--sky)" stroke-width="8"/>
      <text class="price-amount" x="367" y="117" font-size="120" text-anchor="middle" textLength="236" lengthAdjust="spacingAndGlyphs">35€</text>
      <text class="price-label" x="367" y="159" font-size="28" text-anchor="middle">Por sólo</text>
    </g>

    <!-- offer -->
    <text class="offer-main" x="51" y="271" font-size="66" textLength="632" lengthAdjust="spacingAndGlyphs">1000 MEGAS + 100GIGAS</text>
    <text class="offer-sub" x="49" y="324" font-size="52" textLength="636" lengthAdjust="spacingAndGlyphs">MOVIL CON LLAMADAS ILIMITADAS</text>

    <!-- contact band -->
    <path class="contact-band" d="M0,350 L690,334 C745,332 760,398 840,400 L1200,396 V433 H0 Z" fill="var(--yellow)"/>
    <path class="band-wave" d="M690,334 C748,330 770,398 850,398 L1200,394 L1200,400 L845,403 C760,402 745,342 690,340 Z" fill="var(--navy)"/>
    <path class="band-edge" d="M0,348 L690,333" stroke="var(--navy)" stroke-width="4" fill="none"/>

    <g class="phone-icon">
      <circle cx="51" cy="388" r="27" fill="var(--white)"/>
      <path d="M41,377 c2,-2 5,-2 6,0 l3,5 c1,2 0,4 -2,5 l-2,1 c2,5 5,8 10,10 l1,-2 c1,-2 3,-3 5,-2 l5,3 c2,1 2,4 0,6 l-3,3 c-3,2 -9,1 -16,-5 c-7,-6 -10,-13 -9,-17 z"
            fill="var(--navy)"/>
      <path d="M56,374 a12,12 0 0 1 10,10 M55,380 a6,6 0 0 1 5,5" stroke="var(--navy)" stroke-width="2.5" fill="none" stroke-linecap="round"/>
    </g>
    <text class="contact-line" x="94" y="410" font-size="60" textLength="581" lengthAdjust="spacingAndGlyphs">958 47 6620 | ra-vu.es</text>

    <!-- brand -->
    <text class="brand-name" x="712" y="100" font-size="100" textLength="272" lengthAdjust="spacingAndGlyphs">RAVU</text>
    <text class="brand-tagline" x="712" y="133" font-size="24" textLength="272" lengthAdjust="spacingAndGlyphs"><tspan class="tag-light">Wifi | Fibra | </tspan><tspan class="tag-dark">Movil | Tv</tspan></text>
  </g>
</svg>
</body>
</html>
```